Letterhead for Conveyancing Company

Use existing logo to create a letterhead for a conveyancing company. Must be able to be used in Microsoft Word. Easy to read and professional.
Contact information to be at the bottom.
Bright Oak Conveyancing Pty Ltd
ACN 621 984 736PO Box 535 Campbelltown SA 5074
Mobile - 0461739286
Web address - www.brightoakconveyancing.com.au

Requirements
Must have
• Logo and contact details.
• Simple and professional.

```html
<!DOCTYPE html>
<html lang="en">
<head>
<meta charset="utf-8">
<title>Bright Oak Conveyancing – Letterhead</title>
<link rel="stylesheet" href="https://fonts.googleapis.com/css2?family=Roboto:wght@400;500&family=Mulish:wght@700;800&display=swap">
<style>
  :root {
    --brand-pink: #e0409a;
    --brand-grey: #7a7a7a;
    --ink: #555555;
    --ink-strong: #444444;
    --watermark: #f1f1f1;
    --paper: #fafafa;
  }
  * { box-sizing: border-box; margin: 0; padding: 0; }
  html, body { width: 1062px; height: 1200px; overflow: hidden; background: var(--paper); }
  .letterhead {
    position: relative; width: 1062px; height: 1200px; overflow: hidden; background: var(--paper);
    font-family: "Roboto", Arial, sans-serif; color: var(--ink);
  }
  .brand {
    position: absolute; top: 62px; right: 84px; text-align: right;
    font-family: "Mulish", Arial, sans-serif; font-weight: 800; color: var(--brand-grey);
    display: flex; align-items: center; gap: 12px;
  }
  .brand-mark { width: 18px; height: 18px; background: var(--brand-pink); }
  .brand-name { font-size: 46px; line-height: 48px; letter-spacing: -1px; }
  .brand-sub { font-size: 16px; letter-spacing: 4px; line-height: 22px; }
  .watermark {
    position: absolute; top: 430px; left: 140px; width: 780px; text-align: center;
    font-family: "Mulish", Arial, sans-serif; font-weight: 800; color: var(--watermark);
    font-size: 170px; line-height: 170px; letter-spacing: -4px; z-index: 0;
  }
  .content { position: absolute; left: 66px; right: 67px; top: 0; bottom: 0; z-index: 1; }
  .date { position: absolute; top: 295px; font-size: 15px; }
  .recipient { position: absolute; top: 352px; font-size: 15px; line-height: 19.5px; font-style: normal; }
  .recipient strong { font-weight: 500; color: var(--ink-strong); }
  .salutation { position: absolute; top: 468px; font-size: 15px; }
  .body-copy { position: absolute; top: 506px; left: 0; right: 0; }
  .body-copy p {
    font-size: 14.6px; line-height: 19.4px; text-align: justify; margin-bottom: 19px;
  }
  .sign-off { position: absolute; top: 952px; }
  .sign-name { font-size: 15px; font-weight: 500; color: var(--ink-strong); }
  .signature {
    display: block; width: 190px; height: 38px; margin: 6px 0 6px -18px;
    background: linear-gradient(90deg, #e6ebf3, #d7dfeb); border-radius: 4px;
  }
  .sign-role { font-size: 15px; }
  .footer { position: absolute; left: 62px; right: 52px; top: 1098px; }
  .company-name {
    font-family: "Mulish", Arial, sans-serif; font-weight: 700; font-size: 21px;
    color: var(--brand-pink); padding-left: 2px; padding-bottom: 7px;
    border-bottom: 2px solid var(--brand-pink);
  }
  .contact-list {
    list-style: none; display: flex; justify-content: space-between; margin-top: 17px;
    font-size: 15px; color: var(--ink);
  }
  .contact-list li { display: flex; align-items: center; gap: 7px; white-space: nowrap; }
  .contact-list svg { width: 13px; height: 13px; fill: var(--brand-pink); }
</style>
</head>
<body>
<main class="letterhead">
  <div class="brand">
    <span class="brand-mark"></span>
    <div>
      <div class="brand-name">Bright Oak</div>
      <div class="brand-sub">CONVEYANCING</div>
    </div>
  </div>

  <div class="watermark" aria-hidden="true">Bright<br>Oak</div>

  <section class="content">
    <p class="date">30/20/2016</p>
    <address class="recipient">
      <strong>Mr. XYZ Smith</strong><br>
      123, Street No. 123,<br>
      City Name<br>
      Pincode-123456
    </address>
    <p class="salutation">Dear Sir,</p>
    <div class="body-copy">
      <p>Lorem Ipsum is simply dummy text of the printing and typesetting industry. Lorem Ipsum has been the industry's standard dummy text ever since the 1500s, when an unknown printer took a galley of type and scrambled it to make a type specimen book. It has survived not only five centuries, but also the leap into electronic typesetting, remaining essentially unchanged. It was popularised in the 1960s with the release of Lettrix sheets containing Lorem Ipsum passages, and more recently with desktop publishing software like Quillset Composer including versions of Lorem Ipsum.</p>
      <p>Lorem Ipsum is simply dummy text of the printing and typesetting industry. Lorem Ipsum has been the industry's standard dummy text ever since the 1500s, when an unknown printer took a galley of type and scrambled it to make a type specimen book. It has survived not only five centuries, but also the leap into electronic typesetting, remaining essentially unchanged. It was popularised in the 1960s with the release of Lettrix sheets containing Lorem Ipsum passages, and more recently with desktop publishing software like Quillset Composer including versions of Lorem Ipsum.</p>
      <p>Lorem Ipsum is simply dummy text of the printing and typesetting industry. Lorem Ipsum has been the industry's standard dummy text ever since the 1500s, when an unknown printer took a galley of type and scrambled it to make a type specimen book.</p>
      <p>Lorem Ipsum is simply dummy text of the printing and typesetting industry. Lorem Ipsum has been the industry's standard dummy text ever since the 1500s, when an unknown printer took a galley of type and scrambled it to make a type specimen book.</p>
    </div>
    <div class="sign-off">
      <p class="sign-name">Your Name</p>
      <span class="signature" role="img" aria-label="Handwritten signature"></span>
      <p class="sign-role">CEO &nbsp;|&nbsp; Owner</p>
    </div>
  </section>

  <footer class="footer">
    <h2 class="company-name">Bright Oak Conveyancing Pty Ltd</h2>
    <ul class="contact-list">
      <li><svg viewBox="0 0 16 16"><path d="M2 6c1-3 3-4 6-4s5 1 6 4l-3 1-1-2H6L5 7zM3 8h10l1 6H2z"/></svg>0461739286</li>
      <li><svg viewBox="0 0 16 16"><path d="M8 1a7 7 0 1 0 0 14A7 7 0 0 0 8 1zm0 1.5c.8 0 1.7 1.6 2 4H6c.3-2.4 1.2-4 2-4zM2.6 7.5h2.4v1H2.6zm8.4 0h2.4v1H11zM6 9.5h4c-.3 2.4-1.200 4-2 4s-1.7-1.6-2-4z"/></svg>www.brightoakconveyancing.com.au</li>
      <li><svg viewBox="0 0 16 16"><path d="M8 0a5.5 5.5 0 0 0-5.5 5.5C2.5 10 8 16 8 16s5.5-6 5.5-10.5A5.5 5.5 0 0 0 8 0zm0 8a2.5 2.5 0 1 1 0-5 2.5 2.5 0 0 1 0 5z"/></svg>PO Box 871 Marlowdale SA 5096</li>
      <li><svg viewBox="0 0 16 16"><path d="M5 1h2l-.5 4h3L10 1h2l-.5 4H15v2h-3.7l-.4 2H14v2h-3.4L10 15H8l.5-4h-3L5 15H3l.5-4H1V9h2.8l.4-2H2V5h2.5zm1.3 6-.4 2h3l.4-2z"/></svg>ACN 583 217 469</li>
    </ul>
  </footer>
</main>
</body>
</html>
```